New webdesign for a cable company

We need a new design for Lunor Media.

There exist a suggestion for the page, were we have attached files to show you this. The design here is not good enough, but here you can se what content we need.

You can feel free to give adjustment to this design to make it better, our blow us away with a new brilliant design, but from this design you see what content we need.

The important is that the company get a design who represent its products:
- TV = Cable TV
- Bredbånd = Broadband
- Mobil = Mobile phone
- Strøm = Electricity
- Alarm = Alarm
- Lunor Komplett = a cobain pagage of all our products.

Lunor Media would like costumers who visit the site to het the impression that Lunor Media is a professional, innovative and fun company.
Updates

We have to day uploaded pictures of the existing page as the link haven't been working for the most of you as it's placed on a server our developer are using and is often shut it down. 

We have also updated the brief with some new and updated description so please read true the updated brief. 

We will at the same time inform that we haven't been able to give feedback on any of the received design and are sorry for that, we will within the next 24 hours hopefully have started responded the different received designs.

Looking forward to see more suggestion and hope you will help us create and very professional and informative design. 

Reason: We have decided to extend the deadline due to the number of design suggestion who is sent in and your lack of response to all designers due to our own workload.

This project was unfortunately for different reason put on ice for a while, but we are now ready to complete the design and will answer and give feedback too all the received design suggestions. 

Within a couple of days we hope we have answered all you who sent us suggestions, we appreciate all suggestions and hope to get in more suggestions.

Reason: Deisgn description have been updated

Target Market(s)

Our costumer are both private and companies

Industry/Entity Type

Tv

Requirements
Must have
• A easy way to promote and inform about changes in our products, there are a constant change in our products and it must bee a easy and good way to changes ass the marked change. Cheek out this link, for a example of what we like/think of here, https://nett.fjordsignal.no

On all pages there must be a easy way to click on a order button and too inform about your interest (thats two different things), could be placed in the top right corner for example. In the order form you should follow a step by step part:
1. Cheek what product we can provide you.
2. Chooce products.
3. Costumer inforamtion.
4. Confirmation.

Somewere on the portal it must be possible for costumers to log on to their own administration, where they can cheek for invoices, other statuses, etc.

A main menu existing of:
Hjem (Home)
Produkter (Products)
Storkunde (key account/large costumers)
Kundeservice (Costumerservice)
Min side (My page)

The main menu should have the following sub titles:
- Under "Produkter"/products our different products must be listed
- Under "Kundeservice"/Costumerservice it must have these submenus:
- Hjelp og støtte = Help.
- Faktura = Invoice
- Brukerguider = Userguides
- Abbonementavtaler = Terms and conditions.

A bottom menu where we have 5 main categories, with sub categories:
Om oss (about us)
- Om Lunor Media (about Lunor Media)
- Kontaktinformajson ( contact information)
- Pressemeldinger (Pressrelese)
- Ledige stillinger (positions available)
- KRAV ( and organisastion in our field)

Produkter (Product)
- TV (TV)
- Bredbånd (Broadand)
- Telefoni (telephony, both mobil)
- Strøm (elecricity)
- Arlam (Alarm)

Borrettslag/Sameier (Housing cooperatives)
- Løsninger (solutions)
- Produkter (product)
- Kontaktpersoner (contactpersons)

Utbygger (developer)
- Hva vi kan gjøre for dere. (What we can do for you)

Opperatørnett (operators)

Build up the categories and bottom menu something like this:
https://nett.fjordsignal.no
www.brevix.com
Nice to have
• A main menu existing of:
Hjem (Home)
Produkter (Products)
Lunor Media
Kontakt oss (Contact us)

Under "Produkter"/products our different products must be listed and under "Kundeservice"/Costumerservice it must have these submenus:
- Hjelp og støtte = Help.
- Faktura = Invoice
Should not have
• Any translation section since the homepage only will be in Norwegian.

```html
<!DOCTYPE html>
<html lang="no">
<head>
<meta charset="utf-8">
<title>Lunor Media</title>
<link rel="stylesheet" href="https://fonts.googleapis.com/css2?family=Source+Sans+3:wght@400;600;700&family=Open+Sans:wght@600;700&display=swap">
<style>
:root{
  --page:#f4f4f4;
  --panel:#efefef;
  --ink:#333;
  --muted:#666;
  --blue:#2aa3d8;
  --blue-dark:#24649f;
  --tab:#2e7fa5;
  --sub:#3a3a3a;
  --rule:#bdbdbd;
  --foot-top:#4a4c4f;
  --foot-bot:#1b1c1e;
  --white:#fff;
}
*{box-sizing:border-box;margin:0;padding:0}
html,body{width:948px;height:1200px;overflow:hidden}
body{background:var(--page);font-family:"Source Sans 3",Arial,sans-serif;color:var(--ink);position:relative}
.abs{position:absolute}
a{color:inherit;text-decoration:none}

.brand{left:104px;top:12px;display:flex;align-items:center;gap:10px;font-size:30px;font-weight:600;color:var(--blue)}
.brand-mark{width:26px;height:26px;border-radius:50%;background:var(--blue)}

.mainnav{left:107px;top:59px;width:779px;height:31px;border-radius:6px;background:linear-gradient(#fafafa,#e2e2e2);border:1px solid #d8d8d8}
.mainnav a{position:absolute;top:6px;font-size:15px;color:#555;white-space:nowrap}
.mainnav .active{left:112px;top:-8px;width:67px;height:38px;background:var(--tab);color:var(--white);border-radius:3px 3px 0 0;padding-top:14px;text-align:center}
.mainnav .order-btn{right:8px;top:6px;width:166px;height:19px;border:1px solid #ccc;border-radius:5px;background:var(--white);font-size:9px;letter-spacing:.5px;color:#555;text-align:center;line-height:17px}

.subnav{left:219px;top:98px;width:445px;height:21px;background:var(--sub);border-radius:3px;display:flex;justify-content:space-between;padding:0 10px;align-items:center;font-family:"Open Sans",sans-serif;font-size:9.5px;font-weight:700;color:var(--white);letter-spacing:.3px;white-space:nowrap}

.hero-title{left:114px;top:136px;font-size:30px;font-weight:400;letter-spacing:1px;color:var(--blue)}
.hero-tag{left:114px;top:175px;font-size:15px;color:#666}
.hero-list{left:116px;top:224px;list-style:none;font-size:14px;color:var(--blue)}
.hero-list li{height:25px;position:relative;padding-left:14px}
.hero-list li::before{content:"";position:absolute;left:0;top:7px;width:6px;height:6px;border-radius:50%;background:#333}
.hero-btn{left:245px;top:345px;width:92px;height:25px;background:var(--blue);border-radius:4px 0 0 4px;color:var(--white);font-weight:700;font-size:14px;line-height:25px;padding-left:25px}

.tv{left:439px;top:123px;width:446px;height:325px}
.tv-screen{left:453px;top:139px;width:417px;height:245px;background:linear-gradient(135deg,#5e6a60,#8a7460 45%,#a8443c 60%,#6b6f70)}

.products{left:52px;top:453px;width:602px;height:504px}
.products-title{left:102px;top:460px;font-size:21px;font-weight:700;color:var(--blue-dark)}
.dash{left:66px;top:494px;width:586px;border-top:1px dashed #aaa}
.intro{left:92px;top:502px;width:558px;text-align:center;font-size:11.5px;line-height:19px;font-variant:small-caps;letter-spacing:.6px;color:#555}
.card{width:178px}
.card h3{font-size:13px;font-weight:400;color:#333;height:15px;margin-left:4px}
.card .ph{height:64px;border:1px solid #ccc}
.card .more{display:block;text-align:right;font-size:11px;color:#555;margin-top:3px;padding-right:4px}

.side{left:664px;top:453px;width:227px;height:504px;background:var(--panel)}
.side h2{position:absolute;left:25px;font-size:15px;font-weight:700;color:var(--blue-dark)}
.side h2::before{content:"➔";position:absolute;left:-16px;top:2px;font-size:9px;color:#222}
.side .bar{position:absolute;left:4px;width:213px;height:4px;background:#c4c4c4}
.side p{position:absolute;left:6px;width:212px;font-size:9px;line-height:14.2px;color:#666}
.side .rm{position:absolute;left:6px;font-size:10.5px;color:#666}
.check{position:absolute;left:6px;width:212px;display:flex;gap:10px;font-size:8.6px;line-height:10.3px;color:#666}
.box{flex:none;width:12px;height:12px;border:1px solid #bbb;background:#e4e4e4;font-size:10px;line-height:10px;text-align:center;color:#666}

.footer{left:0;top:975px;width:948px;height:225px;background:linear-gradient(var(--foot-top),var(--foot-bot))}
.fcol{position:absolute;top:9px;color:var(--white)}
.fcol h4{font-size:21px;font-weight:400;line-height:24px}
.fcol a{display:block;font-size:9.5px;line-height:20.8px;white-space:nowrap}
.frule{position:absolute;left:126px;width:566px;border-top:1px solid #777}
.copy{position:absolute;left:126px;top:156px;font-size:8.5px;font-weight:600;color:var(--white);white-space:nowrap}
.copy a{color:#4aa7e0;text-decoration:underline;font-weight:400}
.field{position:absolute;left:725px;width:167px;height:19px;background:var(--white);border-radius:4px;font-size:9px;color:#555;padding:4px 7px}
.submit{position:absolute;left:725px;top:182px;width:167px;height:19px;background:linear-gradient(#fff,#ddd);border-radius:4px;font-size:9.5px;font-weight:600;text-align:center;line-height:19px;color:#333}
</style>
</head>
<body>

<a class="abs brand" href="#"><span class="brand-mark"></span>Lunor Media</a>

<nav class="abs mainnav">
  <a style="left:62px" href="#">Hjem</a>
  <a class="active" href="#">Produkter</a>
  <a style="left:197px" href="#">Storkunde</a>
  <a style="left:281px" href="#">Kundeservice</a>
  <a style="left:381px" href="#">Min side</a>
  <a class="order-btn" href="#">:GO TO ORDER:</a>
</nav>

<nav class="abs subnav">
  <a href="#">Om Lunor Media</a><a href="#">Kontaktinformajson</a><a href="#">Pressemeldinger</a><a href="#">Ledige stillinger</a><a href="#">KRAV</a>
</nav>

<h1 class="abs hero-title">LUNOR TV</h1>
<p class="abs hero-tag">Vare TV-kunder har mye a glede seg over.</p>
<ul class="abs hero-list">
  <li>Musikkjeneste og filmleie pa TV-en</li>
  <li>15 valgfrie kanaler</li>
  <li>TV i flere rom kr.0,-*</li>
  <li>Rikt utvalg av ekstrakanaler</li>
</ul>
<a class="abs hero-btn" href="#">Videre</a>

<svg class="abs tv" viewBox="0 0 446 325" aria-hidden="true">
  <ellipse cx="223" cy="318" rx="150" ry="5" fill="#ccc"/>
  <rect x="2" y="2" width="442" height="296" rx="16" fill="#1c1c1c" stroke="#888" stroke-width="2"/>
  <path d="M190 298 h66 l10 16 h-86z" fill="#555"/>
  <rect x="120" y="312" width="206" height="6" rx="3" fill="#222"/>
</svg>
<div class="abs tv-screen" role="img" aria-label="TV programme scene shown on the screen"></div>

<svg class="abs products" viewBox="0 0 602 504" aria-hidden="true">
  <path d="M0 0 H602 V504 C400 480 200 465 60 450 C40 300 30 120 0 0Z" fill="var(--panel)"/>
</svg>
<h2 class="abs products-title">PRODUKTER</h2>
<div class="abs dash"></div>
<p class="abs intro">Lorem ipsum dolor sit amet, consectetuer adipiscing elit, sed diam nonummy nibh euismod tincidunt ut laoreet dolore magna aliquam erat volutpat. Ut wisi enim ad minim veniam, quis nostrud exerci tation ullamcorper suscipit lobortis nisl ut aliquip ex ea commodo consequat.</p>

<div class="abs card" style="left:122px;top:566px"><h3>TV</h3><div class="ph" role="img" aria-label="Woman using a TV menu" style="background:linear-gradient(90deg,#1f3f8a,#3c7bc8 50%,#c7a56c 75%,#b43a2e)"></div><a class="more" href="#">Read More . . .</a></div>
<div class="abs card" style="left:429px;top:566px"><h3>Bredbånd</h3><div class="ph" role="img" aria-label="Globe with connected computers" style="background:radial-gradient(circle at 50% 50%,#c47a2e,#2a5bb0 45%,#1b3478)"></div><a class="more" href="#">Read More . . .</a></div>
<div class="abs card" style="left:122px;top:672px"><h3>Telefoni</h3><div class="ph" role="img" aria-label="Laptop, mobile phone and desk phone" style="background:linear-gradient(#f5f5f5,#d8d8d8)"></div><a class="more" href="#">Read More . . .</a></div>
<div class="abs card" style="left:429px;top:672px"><h3>Strøm</h3><div class="ph" role="img" aria-label="Electric spark between cables" style="background:linear-gradient(90deg,#0d2a6a,#2f6fd0 50%,#0d2a6a)"></div><a class="more" href="#">Read More . . .</a></div>
<div class="abs card" style="left:122px;top:778px"><h3>Arlam</h3><div class="ph" role="img" aria-label="Red alarm bell sign" style="background:linear-gradient(90deg,#cfcfcf,#c42a10 45%,#e2a020 60%,#d6d6d6)"></div><a class="more" href="#">Read More . . .</a></div>
<div class="abs card" style="left:429px;top:778px"><h3>Arlam</h3><div class="ph" role="img" aria-label="Alarm bell icon on red background" style="background:linear-gradient(90deg,#c51c10,#e8a020 50%,#c51c10)"></div><a class="more" href="#">Read More . . .</a></div>

<aside class="abs side">
  <h2 style="top:6px">HJELP OG STØTTE</h2>
  <div class="bar" style="top:21px"></div>
  <p style="top:37px">Lorem ipsum dolor sit amet, consectetuer adipiscing elit, sed diam nonummy nibh euismod tincidunt ut laoreet dolore magna aliquam erat volutpat. Ut wisi enim ad minim veniam, quis nostrud exerci tation ullamcorper suscipit lobortis nisl ut aliquip ex ea commodo consequat.</p>
  <a class="rm" style="top:128px" href="#">➔&nbsp;&nbsp;&nbsp;Read More . . .</a>

  <h2 style="top:172px">ABBONEMENTAVTALER</h2>
  <div class="bar" style="top:195px"></div>
  <div class="check" style="top:212px"><span class="box">✓</span>Lorem ipsum dolor sit amet, consectetuer adipiscing elit, sed diam nonummy nibh euismod tincidunt ut laoreet do.</div>
  <div class="check" style="top:257px"><span class="box">✓</span>Lorem ipsum dolor sit amet, consectetuer adipiscing elit, sed diam nonummy nibh euismod tincidunt ut laoreet dolore magna .</div>
  <div class="check" style="top:300px"><span class="box">✓</span>Lorem ipsum dolor sit amet, consectetuer adipiscing elit, sed diam nonummy nibh euismod tincidunt ut laoreet.</div>

  <h2 style="top:359px">CONTACTPERSONS</h2>
  <div class="bar" style="top:383px"></div>
  <p style="top:400px">Lorem ipsum dolor sit amet, consectetuer adipiscing elit, sed diam nonummy nibh euismod tincidunt ut laoreet dolore magna aliquam erat volutpat. Ut wisi enim ad minim veniam, quis nostrud exerci tation ullamcorper suscipit lobortis nisl ut aliquip ex ea commodo consequat.</p>
</aside>

<footer class="abs footer">
  <div class="fcol" style="left:124px"><h4>Om oss</h4><a href="#">Om Lunor Media</a><a href="#">Kontaktinformajson</a><a href="#">Pressemeldinger</a><a href="#">Ledige stillinger</a><a href="#">KRAV</a></div>
  <div class="fcol" style="left:290px"><h4>Produkter</h4><a href="#">TV</a><a href="#">Bredbånd</a><a href="#">Telefoni</a><a href="#">Strøm</a><a href="#">Arlam</a></div>
  <div class="fcol" style="left:437px"><h4>Borrettslag</h4><a href="#">Løsninger</a><a href="#">Produkter</a><a href="#">Kontaktpersoner</a></div>
  <div class="fcol" style="left:603px"><h4>Produkter</h4><a href="#">TV</a><a href="#">Bredbånd</a><a href="#">Telefoni</a><a href="#">Strøm</a><a href="#">Arlam</a></div>
  <div class="fcol" style="left:728px"><h4>Kontakt oss</h4></div>
  <div class="frule" style="top:146px"></div>
  <p class="copy">Lunor Media is the largest TV distributor and the second largest broadband provider. AS Copyright © 2013 Lunor Media. <a href="#">Brukerguider</a> &amp; <a href="#">Abbonementavtaler</a></p>
  <div class="frule" style="top:178px"></div>
  <div class="field" style="top:40px">Name:</div>
  <div class="field" style="top:61px">Phone:</div>
  <div class="field" style="top:82px">E-mail:</div>
  <div class="field" style="top:103px;height:74px">Messages:</div>
  <div class="submit">Submit</div>
</footer>

</body>
</html>
```